Property Finance Company - Orbin Funding Limited

Background: Orbin Funding Group Limited is a private property finance company. Orbin Funding Group has capital to directly fund first mortgage, mezzanine and preferred equity financing. We also acquire performing, sub-performing and distressed debt.

Orbin Fundings management philosophy emphasises expertise, innovation, wisdom, honesty and competitiveness. Orbin Funding are not finance brokers - we provide debt funding to the commercial property and residential development sectors. Our process is built from experience and cumutavely Orbin Fundings Directors have in excess of 60 years wisdom.

The aim of the website will be to increase brand awareness, provide clients with comfort around our level of skill and background on who we are, generate more sales, and provide examples of projects that we have funded.

The website is a new product launch, and we need to use our Orbin Funding logo that has just been designed. We like a dark background, and either black/silver/grey/ jade green, or black/gold/jade green colours.

Our unique advantages are that we have fast turnaround times, we can solve clients funding problems and we know what we are doing. Our target audience will be viewing the website on both desktop and mobile devices.

We would like to have the following pages:

Home
About
Team
Services
Project Experience
Contact

Competitors Website: http://www.tarvolo.example/

We would also like to have the option of video footage in our website, as you can see in our competitors website.

Overall we want a really slick, elegant but modern website that is better than www.tarvolo.example

Target Market(s)

Finance borrowers, property developers, accountants, lawyers, businesspeople, high net worth people

Industry/Entity Type

Finance

Requirements
Must have
• Please see project description
Nice to have
Should not have

```html
<!DOCTYPE html>
<html lang="en">
<head>
<meta charset="utf-8">
<title>Orbin Funding</title>
<link rel="stylesheet" href="https://fonts.googleapis.com/css2?family=Cinzel:wght@400;700&family=Lato:wght@700;900&family=Open+Sans:wght@400;600;700&display=swap">
<style>
  :root {
    --ink: #272727;
    --dark: #262626;
    --white: #ffffff;
    --silver-text: #2a2a2a;
    --line: #d8d8d8;
    --sky-top: #3f78b4;
    --sky-mid: #8fb3d6;
    --city: #6d7480;
  }
  * { margin: 0; padding: 0; box-sizing: border-box; }
  html, body { width: 1200px; height: 2564px; overflow: hidden; }
  body {
    position: relative;
    background: var(--dark);
    color: var(--white);
    font-family: "Open Sans", Arial, sans-serif;
  }
  .abs { position: absolute; }

  /* Hero */
  .hero { left: 0; top: 0; width: 1200px; height: 638px; }
  .hero-photo {
    position: absolute; inset: 0;
    background:
      linear-gradient(180deg, rgba(0,0,0,0) 55%, rgba(60,66,78,.85) 100%),
      linear-gradient(180deg, var(--sky-top) 0%, var(--sky-mid) 45%, #b9cde0 60%, var(--city) 100%);
  }
  .topbar {
    position: absolute; left: 0; top: 0; width: 1200px; height: 142px;
    background: linear-gradient(180deg, rgba(70,78,88,.85), rgba(90,98,110,.7));
  }
  .brand {
    position: absolute; left: 96px; top: 62px;
    display: flex; align-items: center; gap: 10px;
    font-family: "Cinzel", Georgia, serif; font-size: 24px; font-weight: 400;
    color: var(--white); letter-spacing: 1px;
  }
  .brand-dot { width: 22px; height: 22px; border-radius: 50%; background: var(--white); }
  .social { display: flex; gap: 10px; }
  .social span {
    width: 38px; height: 38px; border: 2px solid var(--white); border-radius: 50%;
  }
  .social-top { right: 100px; top: 21px; }
  .nav {
    right: 100px; top: 90px; display: flex; gap: 42px;
    font-size: 15px; font-weight: 600; letter-spacing: .3px;
  }
  .hero-title {
    left: 0; width: 1200px; top: 228px; text-align: center;
    font-family: "Cinzel", Georgia, serif; font-weight: 700; font-size: 58px;
    letter-spacing: 1px; text-shadow: 0 2px 6px rgba(0,0,0,.35);
  }
  .hero-sub {
    left: 0; width: 1200px; top: 323px; text-align: center;
    font-size: 18px; font-weight: 600;
  }
  .play { left: 557px; top: 430px; }

  /* Silver bands */
  .band { left: 0; width: 1200px; height: 462px; }
  .band svg.bg { position: absolute; inset: 0; }
  .emblem {
    width: 96px; height: 96px; border-radius: 50%;
    background: #7b7b7b;
  }
  .band-title {
    font-family: "Lato", Arial, sans-serif; font-weight: 900;
    font-size: 50px; line-height: 56px; color: var(--silver-text);
  }
  .about { top: 638px; }
  .about .emblem { left: 100px; top: 52px; }
  .about .band-title { left: 98px; top: 168px; }
  .about-copy {
    left: 487px; top: 96px; width: 614px;
    font-size: 15px; line-height: 22px; font-weight: 600; text-align: justify;
    text-shadow: 0 1px 2px rgba(0,0,0,.35);
  }
  .about-copy p + p { margin-top: 14px; }
  .btn {
    left: 487px; top: 302px; width: 138px; height: 54px;
    border: 2px solid var(--white); border-radius: 6px;
    background: rgba(40,40,40,.75);
    font-size: 15px; font-weight: 600; line-height: 50px; text-align: center;
  }

  /* Services */
  .services-title {
    left: 0; width: 1200px; top: 1170px; text-align: center;
    font-family: "Lato", Arial, sans-serif; font-weight: 700; font-size: 28px;
  }
  .services-rule { left: 565px; top: 1226px; width: 70px; height: 2px; background: var(--white); }
  .service { top: 1312px; width: 298px; }
  .service h3 {
    margin-top: 32px;
    font-family: "Lato", Arial, sans-serif; font-weight: 700; font-size: 21px;
  }
  .service p {
    margin-top: 18px; font-size: 13.5px; line-height: 22px; font-weight: 600; text-align: justify;
  }

  /* Team */
  .team { top: 1605px; }
  .team .emblem { left: 100px; top: 64px; }
  .team .band-title { left: 98px; top: 180px; }
  .member { top: 108px; width: 174px; text-align: center; }
  .portrait {
    width: 174px; height: 152px; border: 3px solid var(--white); border-radius: 8px;
    background: linear-gradient(160deg, #8a6a55, #c9a58c 50%, #5a4a40);
  }
  .member h4 {
    margin-top: 26px; font-family: "Lato", Arial, sans-serif; font-weight: 700; font-size: 19px;
    text-shadow: 0 1px 2px rgba(0,0,0,.3);
  }

  /* Footer */
  .footer-brand {
    left: 0; width: 1200px; top: 2215px; display: flex; justify-content: center;
    align-items: center; gap: 12px;
    font-family: "Cinzel", Georgia, serif; font-size: 30px; letter-spacing: 1px;
  }
  .footer-brand .brand-dot { width: 28px; height: 28px; }
  .social-foot { left: 0; width: 1200px; top: 2330px; justify-content: center; }
  .footer-nav {
    left: 0; width: 1200px; top: 2415px; display: flex; justify-content: center; gap: 30px;
    font-family: "Open Sans", Arial, sans-serif; font-weight: 700; font-size: 16px;
  }
  .footer-nav .sep { font-weight: 400; }
  .footer-rule { left: 98px; top: 2476px; width: 1003px; height: 2px; background: var(--line); }
  .copyright {
    left: 0; width: 1200px; top: 2506px; text-align: center; font-size: 15px; font-weight: 600;
  }
</style>
</head>
<body>

<header class="abs hero">
  <div class="hero-photo" role="img" aria-label="City skyline photograph with tall towers under a blue sky"></div>
  <div class="topbar"></div>
  <div class="brand"><span class="brand-dot"></span>ORBIN FUNDING</div>
  <div class="abs social social-top"><span></span><span></span><span></span><span></span></div>
  <nav class="abs nav"><span>HOME</span><span>ABOUT</span><span>TEAM</span><span>SERVICES</span><span>PROJECT EXPERIENCE</span><span>CONTACT</span></nav>
  <h1 class="abs hero-title">ORBIN FUNDING</h1>
  <p class="abs hero-sub">Orbin Funding Group Limited is a private property finance company</p>
  <svg class="abs play" width="86" height="86" viewBox="0 0 86 86" aria-label="Play video">
    <circle cx="43" cy="43" r="39" fill="none" stroke="#fff" stroke-width="5"/>
    <path d="M34 26 L62 43 L34 60 Z" fill="#fff"/>
  </svg>
</header>

<svg width="0" height="0" style="position:absolute">
  <defs>
    <linearGradient id="metal" x1="0" y1="0" x2="0" y2="1">
      <stop offset="0" stop-color="#bcbcbc"/>
      <stop offset=".35" stop-color="#e9e9e9"/>
      <stop offset=".55" stop-color="#8e8e8e"/>
      <stop offset=".75" stop-color="#d6d6d6"/>
      <stop offset="1" stop-color="#f2f2f2"/>
    </linearGradient>
    <linearGradient id="metal-left" x1="0" y1="0" x2="1" y2="1">
      <stop offset="0" stop-color="#c8c8c8"/>
      <stop offset=".5" stop-color="#f0f0f0"/>
      <stop offset="1" stop-color="#cfcfcf"/>
    </linearGradient>
  </defs>
</svg>

<section class="abs band about">
  <svg class="bg" width="1200" height="462" viewBox="0 0 1200 462">
    <path d="M0 0 H1200 V385 Q600 525 0 385 Z" fill="url(#metal)"/>
    <path d="M0 0 H495 C470 200 390 350 165 442 Q70 420 0 385 Z" fill="url(#metal-left)"/>
    <path d="M495 0 C470 200 390 350 165 442" fill="none" stroke="#ffffff" stroke-width="3"/>
    <path d="M497 0 C473 200 394 352 170 444" fill="none" stroke="#333" stroke-width="2"/>
  </svg>
  <div class="abs emblem"></div>
  <h2 class="abs band-title">ORBIN<br>FUNDING</h2>
  <div class="abs about-copy">
    <p>Orbin Funding Group has capital to directly fund first mortgage, mezzanine and preferred equity financing. We also acquire performing, sub-performing and distressed debt. Orbin Fundings management philosophy emphasises expertise, innovation, wisdom, honesty and competitiveness.</p>
    <p>Orbin Funding are not finance brokers - we provide debt funding to the commercial property and residential development sectors. Our process is built from experience and cumutavely Orbin Fundings Directors have in excess of 60 years wisdom.</p>
  </div>
  <div class="abs btn">READ MORE</div>
</section>

<h2 class="abs services-title">OUR SERVICES</h2>
<div class="abs services-rule"></div>

<div class="abs service" style="left:98px">
  <svg width="64" height="58" viewBox="0 0 64 58" aria-hidden="true">
    <path d="M6 28 L30 6 L54 28 M12 22 V52 H40" fill="none" stroke="#fff" stroke-width="5"/>
    <text x="30" y="40" text-anchor="middle" font-family="Open Sans, sans-serif" font-weight="700" font-size="22" fill="#fff">$</text>
    <circle cx="50" cy="46" r="10" fill="none" stroke="#fff" stroke-width="3"/>
    <path d="M45 46 L49 50 L56 42" fill="none" stroke="#fff" stroke-width="3"/>
  </svg>
  <h3>DEVELOPMENT FINANCE</h3>
  <p>Nemo enim ipsam voluptatem quia voluptas sit asperna tur aut odit aut fugit, sed quia consequuntur magni do lores.</p>
</div>
<div class="abs service" style="left:451px">
  <svg width="64" height="58" viewBox="0 0 64 58" aria-hidden="true">
    <circle cx="32" cy="18" r="14" fill="none" stroke="#fff" stroke-width="4"/>
    <text x="32" y="26" text-anchor="middle" font-family="Open Sans, sans-serif" font-weight="700" font-size="20" fill="#fff">$</text>
    <path d="M4 28 Q6 48 26 54 M60 28 Q58 48 38 54" fill="none" stroke="#fff" stroke-width="6" stroke-linecap="round"/>
  </svg>
  <h3>BRIDGING FINANCE</h3>
  <p>Nemo enim ipsam voluptatem quia voluptas sit asperna tur aut odit aut fugit, sed quia consequuntur magni do lores.</p>
</div>
<div class="abs service" style="left:803px">
  <svg width="64" height="58" viewBox="0 0 64 58" aria-hidden="true">
    <circle cx="30" cy="30" r="14" fill="none" stroke="#fff" stroke-width="4"/>
    <text x="30" y="38" text-anchor="middle" font-family="Open Sans, sans-serif" font-weight="700" font-size="20" fill="#fff">$</text>
    <path d="M8 20 V4 M2 10 L8 3 L14 10" fill="none" stroke="#fff" stroke-width="4"/>
    <path d="M50 38 V54 M44 48 L50 55 L56 48" fill="none" stroke="#fff" stroke-width="4"/>
  </svg>
  <h3>BANK FINANCE</h3>
  <p>Nemo enim ipsam voluptatem quia voluptas sit asperna tur aut odit aut fugit, sed quia consequuntur magni do lores.</p>
</div>

<section class="abs band team">
  <svg class="bg" width="1200" height="462" viewBox="0 0 1200 462">
    <path d="M0 0 H1200 V385 Q600 525 0 385 Z" fill="url(#metal)"/>
    <path d="M0 0 H495 C470 200 390 350 165 442 Q70 420 0 385 Z" fill="url(#metal-left)"/>
    <path d="M495 0 C470 200 390 350 165 442" fill="none" stroke="#ffffff" stroke-width="3"/>
    <path d="M497 0 C473 200 394 352 170 444" fill="none" stroke="#333" stroke-width="2"/>
  </svg>
  <div class="abs emblem"></div>
  <h2 class="abs band-title">OUR<br>TEAM</h2>
  <div class="abs member" style="left:495px">
    <div class="portrait" role="img" aria-label="Portrait photo of Tessa Vane"></div>
    <h4>TESSA VANE</h4>
  </div>
  <div class="abs member" style="left:711px">
    <div class="portrait" role="img" aria-label="Portrait photo of Owen Hale"></div>
    <h4>OWEN HALE</h4>
  </div>
  <div class="abs member" style="left:927px">
    <div class="portrait" role="img" aria-label="Portrait photo of Nadia Brook"></div>
    <h4>NADIA BROOK</h4>
  </div>
</section>

<footer>
  <div class="abs footer-brand"><span class="brand-dot"></span>ORBIN FUNDING GROUP</div>
  <div class="abs social social-foot"><span></span><span></span><span></span><span></span><span></span></div>
  <nav class="abs footer-nav">
    <span>HOME</span><span class="sep">|</span><span>ABOUT</span><span class="sep">|</span><span>TEAM</span><span class="sep">|</span><span>SERVICES</span><span class="sep">|</span><span>PROJECT EXPERIENCE</span><span class="sep">|</span><span>CONTACT</span>
  </nav>
  <div class="abs footer-rule"></div>
  <p class="abs copyright">Copyrights © 2017 Orbin Funding. All Rights Reserved</p>
</footer>

</body>
</html>
```